Preschool Website

Looking to have a one page splash with a contact us form that uses some kind of verification to keep bots from filling out the form. We would like for it to be dynamic for both mobile and desktop. Would like to have it show up in search engines for preschool in are area. Would like to include a link to the website are current parents use for payment information.

Target Market(s)

Young Adults with Childrens

Industry/Entity Type

Preschool

Coding

Coded - Design and coding required

Number of Pages Required

1 page

Colors

Designer to choose colors to be used in the design.

Requirements
Must have
• Searchable in Quorla
• Contact us form
• Name
• Phone
• Email
• Message box
• Form must have code entered to submit to prevent junk emails
• Link to the website we use for parents to make payments
• our phone and address clickable on device to make call or map on phone
Should not have
• more then one page

```html
<!DOCTYPE html>
<html lang="en">
<head>
<meta charset="utf-8">
<title>Preschool – Contact</title>
<link rel="stylesheet" href="https://fonts.googleapis.com/css2?family=Paytone+One&family=Poppins:wght@400;500;600&display=swap">
<style>
  :root{
    --green:#17d890;
    --pink:#cc13a0;
    --lavender:#cacdea;
    --panel:#d6d6d6;
    --white:#ffffff;
    --hero-dark:#4e4a45;
    --hero-mid:#6b6660;
    --blocks-dark:#2f2a2c;
  }
  *{box-sizing:border-box;margin:0;padding:0}
  html,body{width:1093px;height:1200px;overflow:hidden}
  body{position:relative;font-family:"Poppins",sans-serif;background:var(--white)}

  .edge{position:absolute;left:0;width:1093px;height:6px;background:var(--green);z-index:5}
  .edge--top{top:0}
  .edge--bottom{bottom:0;height:7px}

  .hero{position:absolute;top:0;left:0;width:1093px;height:647px;overflow:hidden}
  .hero__photo{position:absolute;inset:0;
    background:radial-gradient(ellipse at 80% 60%,#7a6a5a 0%,transparent 55%),
               linear-gradient(180deg,var(--hero-mid) 0%,#5d5852 55%,#6a5546 100%)}
  .hero__stripes{position:absolute;inset:0}

  .logo{position:absolute;left:89px;top:26px;font-family:"Paytone One",sans-serif;font-size:40px;color:var(--green);letter-spacing:1px}

  .contact-form{position:absolute;left:90px;top:102px;width:322px;height:523px;background:var(--panel);border-radius:10px;box-shadow:0 2px 6px rgba(0,0,0,.25);z-index:2}
  .contact-form__field{position:absolute;left:23px;width:274px;height:36px;border:none;border-radius:12px;background:var(--white);
    box-shadow:0 2px 3px rgba(0,0,0,.35);padding:0 33px;font:400 16px "Poppins",sans-serif;color:var(--green)}
  .contact-form__field::placeholder{color:var(--green)}
  .contact-form__field--message{height:146px;padding-top:6px;resize:none}
  .contact-form__submit{position:absolute;left:170px;top:457px;width:127px;height:40px;border:none;border-radius:10px;background:var(--pink);
    color:var(--white);font:500 16px "Poppins",sans-serif}

  .intro{position:absolute;left:571px;top:246px;width:440px;z-index:2}
  .intro__title{font-family:"Paytone One",sans-serif;font-weight:400;font-size:35px;color:var(--green);line-height:46px}
  .intro__text{margin-top:4px;font-size:16px;line-height:23px;color:var(--white)}

  .touch{position:absolute;top:647px;left:0;width:1093px;height:188px;background:var(--lavender);display:flex;align-items:center;justify-content:center}
  .touch__title{font-family:"Paytone One",sans-serif;font-weight:400;font-size:35px;color:var(--pink)}

  .services{position:absolute;top:835px;left:0;width:1093px;height:358px;overflow:hidden}
  .services__photo{position:absolute;inset:0;
    background:linear-gradient(90deg,#4a4648 0%,#5c3f3c 35%,#6a4a3a 60%,#3d4a3e 85%,var(--blocks-dark) 100%)}
  .service__art{position:absolute;border-radius:24px;background:linear-gradient(160deg,#e63dba,#a80f83);opacity:.85}
  .service__button{position:absolute;top:260px;width:255px;height:54px;border-radius:10px;background:var(--pink);color:var(--white);
    font:600 16.5px "Poppins",sans-serif;display:flex;align-items:center;justify-content:center;text-decoration:none}
</style>
</head>
<body>
  <div class="edge edge--top"></div>

  <section class="hero">
    <div class="hero__photo" role="img" aria-label="Classroom desk with books, coloured pencils and ABC blocks"></div>
    <svg class="hero__stripes" width="1093" height="647" viewBox="0 0 1093 647" aria-hidden="true">
      <line x1="330" y1="665" x2="478" y2="535" stroke="var(--green)" stroke-width="28" stroke-linecap="round"/>
      <line x1="405" y1="670" x2="603" y2="482" stroke="var(--pink)" stroke-width="28" stroke-linecap="round"/>
    </svg>

    <div class="logo">LOGO</div>

    <form class="contact-form">
      <input class="contact-form__field" style="top:31px" type="text" placeholder="Your Name">
      <input class="contact-form__field" style="top:95px" type="tel" placeholder="Your Phone">
      <input class="contact-form__field" style="top:159px" type="email" placeholder="Your Email">
      <input class="contact-form__field" style="top:222px" type="text" placeholder="Enter Your Code">
      <textarea class="contact-form__field contact-form__field--message" style="top:286px" placeholder="Your Message"></textarea>
      <button class="contact-form__submit" type="button">Contact Us</button>
    </form>

    <div class="intro">
      <h1 class="intro__title">Communication is key</h1>
      <p class="intro__text">Lorem ipsum dolor sit amet, consectetur adipisicing elit, sed do eiusmod tempor incididunt ut labore et dolore magna aliqua. Ut enim ad minim veniam, quis nostrud exercitation ullamco laboris nisi ut aliquip.</p>
    </div>
  </section>

  <section class="touch">
    <h2 class="touch__title">Get In Touch</h2>
  </section>

  <section class="services">
    <div class="services__photo" role="img" aria-label="Child stacking colourful wooden blocks"></div>

    <div class="service__art" style="left:164px;top:53px;width:173px;height:176px" role="img" aria-label="Illustration of a hand holding a phone beside a contact card"></div>
    <div class="service__art" style="left:453px;top:60px;width:187px;height:153px" role="img" aria-label="Illustration of a folded map with a location pin"></div>
    <div class="service__art" style="left:749px;top:44px;width:198px;height:191px;border-radius:50%" role="img" aria-label="Illustration of a hand paying with a card at a terminal"></div>

    <a class="service__button" style="left:123px" href="#">Get Our Number</a>
    <a class="service__button" style="left:419px" href="#">View Our Addres</a>
    <a class="service__button" style="left:715px" href="#">Make Your Payment</a>
  </section>

  <div class="edge edge--bottom"></div>
</body>
</html>
```